Ductless Mini Split Business Website

Copper Fern Services is looking to design an eye catching educational website about installing Ductless mini splits.

Similar to this company.
https://www.halvikstream.com/

Coding

Coded - Design and coding required

```html
<!DOCTYPE html>
<html lang="en">
<head>
<meta charset="utf-8">
<title>Copper Fern Services – Ductless Experts</title>
<link rel="stylesheet" href="https://fonts.googleapis.com/css2?family=Bebas+Neue&family=Nunito:wght@600;700&family=Open+Sans:ital,wght@0,400;0,600;1,400&family=Oswald:wght@400;500&family=Pathway+Gothic+One&display=swap">
<style>
:root{
  --olive:#4e4a1e;
  --yellow:#f7d324;
  --green:#8dc63f;
  --green-tile:rgba(141,198,63,.93);
  --green-text:#7cb342;
  --blue:#1e3a9e;
  --navy:#13215a;
  --gold:#a46f00;
  --purple:#4b2a8a;
  --grey:#666;
  --white:#fff;
}
*{margin:0;padding:0;box-sizing:border-box}
html,body{width:1200px;height:4263px;overflow:hidden}
body{position:relative;background:var(--white);font-family:"Open Sans",sans-serif;color:var(--grey)}
.abs{position:absolute}
.ph{position:absolute}

/* header */
.topbar{left:0;top:0;width:1200px;height:45px;background:var(--olive)}
.topbar .tag{left:70px;top:15px;font-size:10px;color:#e9e3a0;letter-spacing:.3px}
.btn-quote{left:752px;top:8px;width:136px;height:28px;background:var(--green);color:#fff;font-size:11px;font-family:"Oswald",sans-serif;text-align:center;line-height:28px;border-radius:3px}
.btn-call{left:900px;top:8px;width:154px;height:28px;background:#1c8fe0;color:#fff;font-size:13px;font-family:"Oswald",sans-serif;text-align:center;line-height:28px;border-radius:6px}
.navband{left:0;top:45px;width:1200px;height:63px;background:var(--yellow)}
.nav{left:408px;top:66px;font-family:"Oswald",sans-serif;font-size:14px;color:#3b3b3b}
.nav span{position:absolute;white-space:nowrap}
.logo-card{left:70px;top:55px;width:244px;height:91px;background:#fff;border-radius:6px;box-shadow:0 2px 6px rgba(0,0,0,.25);z-index:5}
.logo-mark{left:16px;top:14px;width:30px;height:30px;border-radius:50%;background:var(--yellow)}
.logo-name{left:54px;top:14px;font-family:"Oswald",sans-serif;font-weight:500;font-size:19px;color:#222;line-height:30px;white-space:nowrap}
.logo-tag{left:0;width:244px;top:56px;text-align:center;font-family:"Oswald",sans-serif;font-weight:500;font-size:19px;color:#111}

/* hero */
.hero{left:0;top:108px;width:1200px;height:604px;background:linear-gradient(180deg,#a9b6c2 0%,#c6ced6 55%,#dde1e4 100%)}
.hero-title{left:0;top:330px;width:1200px;padding-left:170px;text-align:center;font-family:"Bebas Neue",sans-serif;font-weight:400;font-size:60px;line-height:56px;color:var(--yellow);letter-spacing:2px;text-shadow:2px 2px 0 #6b5400}

/* tiles */
.tile{position:absolute;width:311px;background:var(--green-tile);color:#fff;text-align:center}
.tile h3{font-family:"Open Sans",sans-serif;font-weight:400;font-size:23px;line-height:27px;text-transform:uppercase}
.tile p{font-size:9.5px;font-style:italic;line-height:15px;margin-top:10px;padding:0 18px}
.tile svg{display:block;margin:0 auto 12px}

/* mini split band */
.splitband{left:0;top:1068px;width:1200px;height:388px;background:linear-gradient(90deg,#d8d8d8,#f2f2f2 60%,#e6e6e6)}
.split-title{left:520px;width:600px;top:1152px;text-align:center;font-family:"Nunito",sans-serif;font-weight:700;font-size:44px;color:var(--blue)}
.split-sub{left:520px;width:600px;top:1203px;text-align:center;font-family:"Nunito",sans-serif;font-weight:600;font-size:31px;line-height:38px;color:var(--blue)}
.btn-learn{left:737px;top:1307px;width:168px;height:43px;background:var(--navy);border-radius:6px;color:#fff;font-size:14px;text-align:center;line-height:43px;letter-spacing:.5px}
.thumb{position:absolute;top:1415px;width:232px;height:125px;border:5px solid #fff;box-shadow:0 2px 5px rgba(0,0,0,.2)}

/* about */
.about{left:0;top:1561px;width:1200px;height:314px;background:var(--gold)}
.about-title{left:58px;top:1596px;font-family:"Bebas Neue",sans-serif;font-weight:400;font-size:58px;line-height:60px;color:var(--yellow);letter-spacing:1px;white-space:nowrap}
.about-text{left:58px;top:1671px;width:488px;font-family:"Pathway Gothic One",sans-serif;font-size:21px;line-height:25.5px;color:#fff;text-align:justify}
.diagram{left:581px;top:1585px;width:561px;height:264px;background:linear-gradient(135deg,#f4f6fb,#e3e8f3);border-radius:8px}

/* services grid */
.svc h3{position:absolute;text-align:center;font-weight:400;font-size:23px;line-height:26px;color:var(--green-text);width:314px}
.svc p{position:absolute;width:314px;font-size:13px;line-height:27.5px;color:#777;text-align:justify}
.svc ul{position:absolute;font-size:13.5px;font-style:italic;color:var(--green-text);line-height:28px;padding-left:20px}
.prod{position:absolute;background:linear-gradient(90deg,#c8c8c8,#f4f4f4 50%,#bdbdbd)}

/* why choose */
.why{left:0;top:2800px;width:1200px;height:639px;background:var(--purple)}
.why-title{left:92px;top:2880px;width:430px;font-family:"Bebas Neue",sans-serif;font-weight:400;font-size:50px;line-height:63px;color:var(--green);letter-spacing:1px;white-space:nowrap}
.why-item h4{position:absolute;left:157px;font-weight:400;font-size:19px;line-height:25px;color:#fff;width:350px}
.why-item p{position:absolute;left:157px;width:355px;font-size:12.5px;line-height:25px;color:#fff}
.why-icon{position:absolute;left:90px;width:42px;height:42px}
.form{left:538px;top:2886px;width:578px;height:527px;background:#fff}
.form h5{position:absolute;left:36px;top:36px;font-weight:400;font-size:17px;color:var(--green-text)}
.form label{position:absolute;left:36px;font-size:10px;color:#555}
.form label b{color:#d33;font-weight:400}
.form .field{position:absolute;left:36px;width:356px;height:14px;background:#eee;font-size:9px;color:#aaa;padding-left:14px;line-height:14px}
.form .area{position:absolute;left:36px;width:520px;height:79px;background:#eee;font-size:11px;color:#aaa;padding:10px 16px}
.btn-est{position:absolute;left:36px;top:382px;width:134px;height:45px;background:#52c15a;color:#fff;font-size:11px;font-weight:600;text-align:center;line-height:12px;padding-top:10px}

/* testimonials */
.ice{left:0;top:3439px;width:1200px;height:442px;background:linear-gradient(180deg,#e6f4fb,#bfe1f3 45%,#d8eef9)}
.card{position:absolute;top:3464px;width:488px;height:199px;background:#fff;border:1px solid #b9d9ec;text-align:center}
.card .kicker{margin-top:26px;font-size:9px;letter-spacing:2px;color:#888;text-transform:uppercase}
.card h4{font-family:"Nunito",sans-serif;font-weight:700;font-size:24px;line-height:30px;color:#2b3a8a;margin-top:8px}
.card h4 span{color:#b4232a}
.card p{font-size:8px;line-height:12px;color:#777;padding:0 50px;margin-top:12px}
.quote p{font-style:italic;margin-top:78px;padding:0 40px;font-size:8.5px;line-height:13px;color:#777}
.quote small{display:block;color:#c07a00;font-size:7px;margin-top:4px}
.arrow{position:absolute;top:3578px}
.brand{position:absolute;top:3748px;font-family:"Oswald",sans-serif;font-weight:500;font-size:52px;line-height:56px}

/* footer */
.footer{left:0;top:3881px;width:1200px;height:382px;background:linear-gradient(90deg,#13208f 0%,#1d2eb0 35%,#7a1e7a 62%,#d11d1d 100%)}
.footer-logo{left:154px;top:3922px;width:215px;height:111px;background:#fff;border-radius:6px}
.footer-logo .logo-mark{left:14px;top:18px;width:26px;height:26px}
.footer-logo .logo-name{left:48px;top:16px;font-size:16px;line-height:30px}
.footer-logo .logo-tag{width:215px;top:62px;font-size:17px}
.fh{position:absolute;top:3952px;font-size:12.5px;font-weight:600;color:#fff;letter-spacing:1px}
.news{position:absolute;left:400px;width:180px}
.news .img{position:absolute;left:0;top:0;width:70px;height:66px}
.news p{position:absolute;left:86px;top:0;width:100px;font-size:10.5px;line-height:15px;color:#fff}
.areas{left:640px;top:3996px;width:200px;font-size:10.5px;line-height:16px;color:#fff}
.areas ul{list-style:none;margin-top:18px}
.social{position:absolute;top:3989px;width:32px;height:32px;background:#fff;border-radius:3px}
</style>
</head>
<body>

<!-- Header -->
<div class="abs topbar"><span class="abs tag">YOUR DUCTLESS MINI-SPLIT AND BOILER EXPERTS!</span></div>
<div class="abs btn-quote">REQUEST A QUOTE</div>
<div class="abs btn-call">CALL 555-203-4188</div>
<div class="abs navband"></div>
<nav class="abs nav" aria-label="Main">
  <span style="left:0">HOME</span>
  <span style="left:84px">ABOUT US</span>
  <span style="left:183px">DUCTLESS HEAT PUMPS</span>
  <span style="left:364px">FAQ</span>
  <span style="left:428px">FINANCING</span>
  <span style="left:548px">REVIEWS</span>
  <span style="left:652px">CONTACT US</span>
</nav>
<div class="abs logo-card">
  <span class="abs logo-mark"></span>
  <span class="abs logo-name">Copper Fern Services</span>
  <span class="abs logo-tag">DUCTLESS EXPERTS</span>
</div>

<!-- Hero -->
<div class="ph hero" role="img" aria-label="Bright living room with a wall-mounted ductless unit above a grey sofa, a floor lamp and a potted plant"></div>
<h1 class="abs hero-title">Ductless Mini Splits Installation<br>Services Since 1999</h1>

<!-- Service tiles -->
<div class="tile" style="left:94px;top:574px;height:232px;padding-top:28px">
  <svg width="60" height="40" viewBox="0 0 60 40"><rect x="4" y="4" width="52" height="16" rx="3" fill="none" stroke="#fff" stroke-width="2.5"/><path d="M12 26v10M22 26v10M32 26v10M42 26v10" stroke="#fff" stroke-width="2.5"/></svg>
  <h3>Ductless A/C &amp; Heat<br>Pump Installations</h3>
  <p>Need a ductless system installed?<br>We are your ductless mini-split experts!</p>
</div>
<div class="tile" style="left:424px;top:574px;height:232px;padding-top:20px">
  <svg width="56" height="56" viewBox="0 0 56 56"><path d="M10 46L40 16M16 10l30 30" stroke="#fff" stroke-width="6" stroke-linecap="round"/><circle cx="42" cy="14" r="7" fill="none" stroke="#fff" stroke-width="4"/></svg>
  <h3>Start-Up and<br>Commissioning</h3>
  <p>Did you purchase a ductless system online?<br>Let us do the start up and commissioning!</p>
</div>
<div class="tile" style="left:753px;top:574px;height:232px;padding-top:20px">
  <svg width="40" height="56" viewBox="0 0 40 56"><rect x="10" y="4" width="22" height="44" rx="4" fill="#fff"/><circle cx="10" cy="22" r="7" fill="#fff"/></svg>
  <h3>Boiler &amp; Combi<br>Boiler Installations</h3>
  <p>Need a boiler system installed?<br>We are your boiler experts!</p>
</div>
<div class="tile" style="left:94px;top:821px;height:230px;padding-top:28px">
  <svg width="70" height="40" viewBox="0 0 70 40"><rect x="4" y="12" width="62" height="20" rx="4" fill="#fff"/><path d="M52 2l2 5M60 4l-3 5" stroke="#fff" stroke-width="2"/></svg>
  <h3>Ductless System<br>Cleanings</h3>
  <p>Professional cleaning services for your ductless system</p>
</div>
<div class="tile" style="left:424px;top:821px;height:230px;padding-top:26px">
  <svg width="70" height="48" viewBox="0 0 70 48"><rect x="4" y="4" width="40" height="10" fill="#fff"/><rect x="4" y="18" width="40" height="10" fill="#fff"/><rect x="4" y="32" width="40" height="10" fill="#fff"/><path d="M58 8v16M50 16h16M52 10l12 12M64 10L52 22" stroke="#fff" stroke-width="2"/></svg>
  <h3>Server Room<br>Cooling</h3>
  <p>Server room and data centre cooling with powerful ductless A/C systems</p>
</div>
<div class="tile" style="left:753px;top:821px;height:230px;padding-top:22px">
  <svg width="52" height="50" viewBox="0 0 52 50"><polygon points="26,2 32,19 50,19 35,30 41,48 26,37 11,48 17,30 2,19 20,19" fill="#fff"/></svg>
  <h3>Interactive Remote</h3>
  <p>See what it feels like to be using the remote to control your ductless system. Your portable thermostat!</p>
</div>

<!-- Mini-split band -->
<div class="ph splitband" role="img" aria-label="Woman holding a remote below a wall-mounted ductless unit"></div>
<h2 class="abs split-title">Ductless Mini-Splits</h2>
<p class="abs split-sub">The most efficient air conditioning<br>and heating for your home</p>
<div class="abs btn-learn">LEARN MORE ▸</div>
<div class="thumb" style="left:127px;background:linear-gradient(180deg,#6b6f76,#c9c2b8)" role="img" aria-label="Bedroom with a ductless unit"></div>
<div class="thumb" style="left:375px;background:linear-gradient(180deg,#e9e4dc,#b48a5e)" role="img" aria-label="Room with a ceiling cassette"></div>
<div class="thumb" style="left:624px;background:linear-gradient(180deg,#d9cfbf,#7d6a55)" role="img" aria-label="Open kitchen and dining area"></div>
<div class="thumb" style="left:873px;background:linear-gradient(180deg,#ede8e1,#b98d61)" role="img" aria-label="Room with a ceiling cassette"></div>

<!-- About -->
<div class="abs about"></div>
<h2 class="abs about-title">Copper Fern Services</h2>
<p class="abs about-text">We are also the experts when it comes to unparalleled ductless solutions. Whether you need repairs or maintenance for an existing unit or are considering switching your baseboard heating with a ductless heat pump, our trained technicians can do it all. With over 21 years of industry experience, we have proudly cared for the ductless needs of hundreds of residential properties throughout Oregon</p>
<div class="ph diagram" role="img" aria-label="Illustration of single-zone and multi-zone ductless systems, outdoor units piped to indoor wall units"></div>

<!-- Services grid -->
<section class="svc">
  <h3 style="left:116px;top:1918px">DUCTLESS MINI-SPLITS</h3>
  <p style="left:116px;top:1961px">High efficiency ductless air conditioners and heat pumps that can both cool and heat all year long. We have systems suitable for homes, offices, and server rooms.</p>
  <ul style="left:124px;top:2101px"><li>Kestrel K-Series</li><li>Q-Series &amp; Metro-Multi</li><li>Norvane Calmline</li><li>Aerilo</li><li>Brightwell</li><li>Lumo</li></ul>
  <div class="prod" style="left:342px;top:2101px;width:88px;height:170px" role="img" aria-label="Silver ductless outdoor unit"></div>

  <h3 style="left:447px;top:1918px">HOT WATER TANKS</h3>
  <p style="left:447px;top:1961px">Our best in class hot water tanks will suit any size home and provide hot water reliably and efficiently. Pair with a boiler to heat your home &amp; water simultaneously.</p>
  <ul style="left:455px;top:2101px"><li>Prism Coil Indirect Tanks</li><li>Prism Coil Smart</li><li>Veldhaus Tankline</li></ul>
  <div class="prod" style="left:673px;top:2101px;width:86px;height:170px;border-radius:10px" role="img" aria-label="White indirect hot water tank"></div>

  <h3 style="left:778px;top:1918px">BOILERS &amp; COMBI<br>BOILERS</h3>
  <p style="left:778px;top:1988px">We sell, install and service a wide range of boilers including combination and wall-hung. We have the right boiler for your needs, be it a residential home or a large office complex.</p>
  <ul style="left:786px;top:2127px"><li>Toravi</li><li>Veldhaus</li><li>Marlow</li><li>Thermik</li><li>Prism Coil</li></ul>
  <div class="prod" style="left:1004px;top:2128px;width:86px;height:170px" role="img" aria-label="Wall-hung combi boiler"></div>

  <h3 style="left:116px;top:2319px">TANKLESS WATER<br>HEATERS</h3>
  <p style="left:116px;top:2389px">We install the most efficient tankless water heaters in the Canadian market today! This results in dramatic reduction of carbon dioxide and increases the heater's efficiency level to over 93%! Some other brands may have a bit higher efficiency ratings, but there is a fine balance between the efficiency level and flow rate performance.</p>
  <div class="prod" style="left:340px;top:2598px;width:90px;height:168px" role="img" aria-label="Tankless water heater"></div>

  <h3 style="left:447px;top:2319px">GAS FIREPLACES</h3>
  <p style="left:447px;top:2362px">Hearthline fireplaces are energy efficient, do not require power to heat your home and come in a wide variety of styles and options. So you can be sure that there is a Hearthline Fireplace for you and let <i>coolsplit.ca</i> help with your choice!</p>
  <ul style="left:455px;top:2572px"><li>Hearthline</li><li>Emberline Log Sets</li></ul>
  <div class="prod" style="left:671px;top:2545px;width:88px;height:172px;background:linear-gradient(180deg,#3a3a3a,#c8621b 70%,#2a2a2a);border-radius:40px 40px 0 0" role="img" aria-label="Arched gas fireplace with flames"></div>

  <h3 style="left:778px;top:2319px">SOLAR HEATING</h3>
  <p style="left:778px;top:2362px">As the cleanest, most abundant and easily accessible form of energy on earth, start your sustainable energy approach with solar energy. A solar system not only showcases your commitment to the environment, it will increase your property value at the same time.</p>
  <ul style="left:786px;top:2629px"><li>Veldhaus Sunline</li></ul>
  <div class="prod" style="left:1003px;top:2597px;width:88px;height:176px" role="img" aria-label="White solar heating controller unit"></div>
</section>

<!-- Why choose -->
<div class="abs why"></div>
<h2 class="abs why-title">Why Choose<br>Copper Fern Services ?</h2>
<div class="why-item">
  <svg class="why-icon" style="top:3040px" viewBox="0 0 42 42"><rect x="6" y="4" width="24" height="32" fill="none" stroke="#8dc63f" stroke-width="2"/><path d="M11 12h14M11 18h14M11 24h8" stroke="#8dc63f" stroke-width="2"/></svg>
  <h4 style="top:3039px">0% Financing for 60 months</h4>
  <p style="top:3070px">Providing options to our customers where it matters most. Offer applies to Crestair systems.</p>
  <svg class="why-icon" style="top:3145px" viewBox="0 0 42 42"><path d="M4 20a17 17 0 0 1 34 0z" fill="none" stroke="#8dc63f" stroke-width="2"/><path d="M21 20v14a4 4 0 0 1-8 0" fill="none" stroke="#8dc63f" stroke-width="2"/></svg>
  <h4 style="top:3146px">365 Day, Money Back Guarantee</h4>
  <p style="top:3177px">We have integrity, and stand behind our services to ensure that you are satisfied.</p>
  <svg class="why-icon" style="top:3250px" viewBox="0 0 42 42"><circle cx="21" cy="14" r="9" fill="none" stroke="#8dc63f" stroke-width="2"/><path d="M6 38c2-9 8-13 15-13s13 4 15 13" fill="none" stroke="#8dc63f" stroke-width="2"/></svg>
  <h4 style="top:3251px">We Are the Experts in Ductless<br>Services</h4>
  <p style="top:3306px">Not only can we perform the services with precision, but we can also educate you on why ductless is the way to do.</p>
</div>
<form class="abs form">
  <h5>BOOK AN APPOINTMENT HERE!</h5>
  <label style="top:112px">Name <b>*</b></label><div class="field" style="top:132px"></div>
  <label style="top:166px">Email <b>*</b></label><div class="field" style="top:188px;width:362px">Your best email address</div>
  <label style="top:219px">Address <b>*</b></label><div class="field" style="top:244px"></div>
  <label style="top:273px">Please Describe Your Request <b>*</b></label><div class="area" style="top:292px">Message</div>
  <div class="btn-est">Get Your Free<br>Estimate</div>
</form>

<!-- Testimonials & partners -->
<div class="ph ice" role="img" aria-label="Pale blue frosty background with snow drift"></div>
<div class="card" style="left:86px">
  <div class="kicker">Air Conditioning &amp; Heating Services</div>
  <h4>Specializing In<br><span>Ductless Air Conditioning</span></h4>
  <p>We specialize in designing and installing complete ductless comfort systems for both residential and commercial markets, as well as service and maintenance of those systems. Strong pride is taken in the craftsmanship that we instill in each of our employees. Give us a call for your air conditioning and heating needs.</p>
</div>
<div class="card quote" style="left:596px">
  <p>Dana and his team were very professional and fantastic to work with. Very patient in helping us consider multiple options and very reasonable with price. We bought a unit to supplement an inadequate forced air system in an old home where heat and cooling wouldn't reach the top floor. A single unit is now cooling the entire top floor and some of the main floor.<small>Rowan<br>Toronto, ON</small></p>
</div>
<svg class="arrow" style="left:54px" width="16" height="22" viewBox="0 0 16 22"><path d="M13 2L4 11l9 9" fill="none" stroke="#2b3a6a" stroke-width="3"/></svg>
<svg class="arrow" style="left:1098px" width="16" height="22" viewBox="0 0 16 22"><path d="M3 2l9 9-9 9" fill="none" stroke="#2b3a6a" stroke-width="3"/></svg>
<span class="brand" style="left:104px;color:#6b6b6b">Lumo</span>
<span class="brand" style="left:310px;color:#c41e2a">Norvane</span>
<div class="ph" style="left:500px;top:3720px;width:170px;height:160px;background:radial-gradient(ellipse at center,#f4f8fb 0%,#aac8e6 70%,rgba(170,200,230,0) 72%)" role="img" aria-label="Cartoon polar bear mascot"></div>
<span class="brand" style="left:692px;top:3758px;font-size:34px;color:#0f3ea8">Brightwell</span>
<span class="brand" style="left:898px;color:#1a2a6c">Toravi</span>

<!-- Footer -->
<div class="abs footer"></div>
<div class="abs footer-logo">
  <span class="abs logo-mark"></span>
  <span class="abs logo-name">Copper Fern Services</span>
  <span class="abs logo-tag">DUCTLESS EXPERTS</span>
</div>
<div class="fh" style="left:400px">RECENT NEWS</div>
<div class="news" style="top:3994px"><div class="img" style="background:linear-gradient(180deg,#7a8fa8,#3d3a2e)" role="img" aria-label="House at dusk"></div><p>Port Neches, TX Ductless Air Conditioner Installation</p></div>
<div class="news" style="top:4069px"><div class="img" style="background:linear-gradient(180deg,#b46a1c,#3b1f10)" role="img" aria-label="Facts versus myths graphic"></div><p>BUSTING MYTHS ABOUT ELECTRIC &amp; DUCTLESS HEAT PUMPS</p></div>
<div class="news" style="top:4146px"><div class="img" style="background:linear-gradient(180deg,#9fb6c8,#5f7a4e)" role="img" aria-label="Older two-storey house"></div><p>Ductless Heating And Cooling In A Century-Old Nederland, TX Home</p></div>
<div class="fh" style="left:640px">AREAS SERVED</div>
<div class="abs areas">We proudly offer our services to the following areas:
  <ul><li>• BEAUMONT, TX</li><li>• BRIDGE CITY, TX</li><li>• GROVES, TX</li><li>• NEDERLAND, TX</li><li>• ORANGE, TX</li><li>• PORT ARTHUR, TX</li><li>• PORT NECHES, TX</li></ul>
</div>
<div class="fh" style="left:879px">FOLLOW US</div>
<span class="social" style="left:884px"></span>
<span class="social" style="left:926px"></span>
<span class="social" style="left:968px"></span>

</body>
</html>
```